Pages That Pay Dividends - book cover (front panel only)

I want a book cover (for print and ebook) in a distinctive, quirky style that can be repurposed for podcast artwork too. Full brief supplied.
The book is a practical, accessible handbook for anyone thinking about writing a book to build their business, with a wide range of tips and techniques to help plan, write, publishing and promote a book that’s integrated with your platform and works to build your reputation, network and credibility from day 1.
The target audience is experts in business, particularly owners of SMEs with an established online and offline platform (eg speaking, training, consulting) who want to add a book to take their business to the next level.
I want the design to be strong and distinctive, slightly quirky without being gimmicky, with the focus on typography.

Target Market(s)

Those writing a book based on their expertise to build their business

Industry/Entity Type

Publishing Company

Font styles to use
Serif
Sans Serif
Decorative

Colors

Designer to choose colors to be used in the design.

Requirements
Must have
• Commercially appealing book cover design, with application files and copyright supplied, front panel only, 5.5 x 8.5 inch format. Must work at both full size and thumbnail.
Nice to have
• A distinctive style that could be applied across other products in my portfolio.

```html
<!DOCTYPE html>
<html lang="en">
<head>
<meta charset="utf-8">
<title>Pages That Pay Dividends – Book Cover</title>
<link rel="stylesheet" href="https://fonts.googleapis.com/css2?family=Roboto+Condensed:wght@700&family=Montserrat:wght@700&display=swap">
<style>
  :root {
    --ink: #000000;
    --olive: #a9bf3c;
    --olive-dark: #9ab234;
    --teal: #1fd9a3;
    --bubble-text: #1c1c1a;
    --white: #ffffff;
    --sepia-pale: #e6d6bd;
    --sepia-light: #c2a684;
    --sepia-mid: #7c6349;
    --sepia-dark: #3a2c1e;
    --sepia-deep: #140e08;
  }
  html, body {
    margin: 0;
    padding: 0;
    width: 776px;
    height: 1200px;
    overflow: hidden;
    background: var(--ink);
  }
  .cover {
    position: relative;
    width: 776px;
    height: 1200px;
    background: var(--ink);
    overflow: hidden;
  }
  .cover-photo {
    position: absolute;
    left: 0;
    top: 0;
    width: 776px;
    height: 1200px;
  }
  .layer {
    position: absolute;
    left: 0;
    top: 0;
    width: 776px;
    height: 1200px;
  }
  .photo-glow {
    background:
      radial-gradient(ellipse 300px 260px at 600px 700px, var(--sepia-light) 0%, rgba(124,99,73,0.85) 45%, rgba(20,14,8,0) 100%),
      radial-gradient(ellipse 380px 420px at 560px 780px, rgba(124,99,73,0.9) 0%, rgba(58,44,30,0.7) 55%, rgba(20,14,8,0) 100%),
      radial-gradient(ellipse 260px 120px at 700px 560px, rgba(194,166,132,0.7) 0%, rgba(20,14,8,0) 100%);
  }
  .photo-paper {
    background:
      radial-gradient(ellipse 420px 70px at 300px 1010px, var(--sepia-pale) 0%, rgba(194,166,132,0.75) 40%, rgba(20,14,8,0) 100%),
      linear-gradient(180deg, rgba(0,0,0,0) 0%, rgba(0,0,0,0) 940px, rgba(124,99,73,0.5) 1000px, rgba(58,44,30,0.6) 1050px, var(--ink) 1100px);
  }
  .photo-diagonal {
    background: linear-gradient(118deg, rgba(0,0,0,0) 52%, rgba(58,44,30,0.55) 60%, rgba(0,0,0,0) 68%);
    top: 280px;
    height: 700px;
  }
  .title, .callout, .byline {
    position: absolute;
    left: 0;
    top: 0;
  }
  .title text {
    font-family: "Roboto Condensed", sans-serif;
    font-weight: 700;
    text-transform: uppercase;
  }
  .title .title-lead { fill: var(--olive); }
  .title .title-main { fill: var(--teal); }
  .callout .bubble { fill: var(--olive); }
  .callout .bubble-shade { fill: var(--olive-dark); }
  .subtitle {
    position: absolute;
    left: 96px;
    top: 314px;
    width: 380px;
    margin: 0;
    font-family: "Roboto Condensed", sans-serif;
    font-weight: 700;
    font-size: 28px;
    line-height: 40px;
    letter-spacing: 0.5px;
    text-align: center;
    text-transform: uppercase;
    color: var(--bubble-text);
  }
  .byline text {
    font-family: "Montserrat", sans-serif;
    font-weight: 700;
    font-size: 64px;
    letter-spacing: 3px;
    text-transform: uppercase;
    fill: var(--white);
  }
</style>
</head>
<body>
<main class="cover">
  <div class="cover-photo" role="img" aria-label="Sepia photograph of a hand holding a fountain pen, writing on a lit sheet of paper against a dark background">
    <div class="layer photo-glow"></div>
    <div class="layer photo-diagonal"></div>
    <div class="layer photo-paper"></div>
  </div>

  <svg class="title" width="776" height="270" viewBox="0 0 776 270" aria-label="Pages That Pay Dividends">
    <text class="title-lead" x="84" y="115" font-size="92" textLength="616" lengthAdjust="spacingAndGlyphs">Pages That Pay</text>
    <text class="title-main" x="84" y="255" font-size="162" textLength="616" lengthAdjust="spacingAndGlyphs">Dividends</text>
  </svg>

  <svg class="callout" width="776" height="540" viewBox="0 0 776 540" aria-hidden="true">
    <polygon class="bubble" points="80,300 492,280 492,478 460,478 457,521 404,492 80,492"/>
    <polygon class="bubble-shade" points="492,380 492,478 460,478 457,521 404,492 180,492"/>
  </svg>

  <p class="subtitle">Clever ways to plan<br>and write a book<br>that works harder<br>for your business</p>

  <svg class="byline" width="776" height="1200" viewBox="0 0 776 1200">
    <text x="388" y="1158" text-anchor="middle">Maren Holt</text>
  </svg>
</main>
</body>
</html>
```